Letter and Envelope Design For Harborline Realty

Please design a letter and an envelope incorporating our logo (See Attached). We are also launched a business card contest. Since we want them to match, please feel free to submit a design for both the business card and also the letter design and envelope.

Requirements
Must have
• The envelope, the letter and the business cards must match somehow connecting the designs. We want them to have something that holds them together besides the logo.

```html
<!DOCTYPE html>
<html lang="en">
<head>
<meta charset="utf-8">
<title>Harborline Realty Stationery</title>
<link href="https://fonts.googleapis.com/css2?family=Montserrat:wght@500;600&family=PT+Sans:wght@400;700&display=swap" rel="stylesheet">
<style>
  :root {
    --brand-blue: #0d1a8c;
    --brand-grey: #58595b;
    --ink: #2b2b2b;
    --paper: #fbfbfb;
    --backdrop: #ebebeb;
    --rule: #c9c9c9;
  }
  * { box-sizing: border-box; margin: 0; padding: 0; }
  html, body { width: 1200px; height: 825px; overflow: hidden; }
  body { background: var(--backdrop); font-family: "PT Sans", Arial, sans-serif; color: var(--ink); position: relative; }
  .sheet { position: absolute; background: var(--paper); overflow: hidden; }

  .header-accent {
    position: absolute; right: 0; top: 0;
    background: linear-gradient(90deg, rgba(13,26,140,0) 0%, rgba(13,26,140,0.55) 55%, rgba(88,89,91,0.75) 100%);
  }

  .brand { position: absolute; display: flex; align-items: center; }
  .brand-circle { border: 2.5px solid var(--brand-blue); border-radius: 50%; flex: none; }
  .brand-name { font-family: "Montserrat", sans-serif; font-weight: 600; color: var(--brand-blue); letter-spacing: 0.12em; line-height: 1.25; text-transform: uppercase; }

  /* Letterhead */
  .letterhead { left: 80px; top: 78px; width: 471px; height: 667px; }
  .letterhead .header-accent { width: 220px; height: 52px; }
  .letterhead .brand { left: 32px; top: 24px; }
  .letterhead .brand-circle { width: 48px; height: 48px; margin-right: 8px; }
  .letterhead .brand-name { font-size: 14px; }
  .letter-contact { position: absolute; left: 340px; top: 62px; border-left: 1px solid var(--brand-grey); padding-left: 8px; font-size: 7.6px; line-height: 9.2px; color: #333; }
  .letter-contact .row { display: flex; align-items: center; gap: 3px; }
  .letter-contact .addr { margin-top: 4px; color: #555; }
  .icon { width: 6px; height: 6px; fill: var(--brand-blue); flex: none; }
  .letter-body { position: absolute; left: 30px; top: 198px; width: 412px; }
  .salutation { font-family: Arial, sans-serif; font-weight: 700; font-size: 10.5px; margin-bottom: 14px; }
  .letter-body p { font-size: 10px; line-height: 12.4px; text-align: justify; margin-bottom: 12.2px; color: #333; }
  .signature { position: absolute; left: 30px; top: 548px; width: 76px; height: 36px; background: linear-gradient(90deg, #e4e4e4, #d3d3d3); border-radius: 4px; }

  /* Business card front */
  .card-front { left: 630px; top: 94px; width: 200px; height: 114px; }
  .card-front .header-accent { width: 90px; height: 24px; }
  .card-front .brand { left: 10px; top: 10px; }
  .card-front .brand-circle { width: 22px; height: 22px; border-width: 1.5px; margin-right: 4px; }
  .card-front .brand-name { font-size: 6.4px; }
  .card-holder { position: absolute; right: 11px; top: 35px; text-align: right; }
  .card-holder .name { font-weight: 700; font-size: 7px; color: var(--brand-blue); text-transform: uppercase; }
  .card-holder .role { font-size: 5px; color: #777; }
  .card-contact { position: absolute; left: 10px; top: 88px; font-size: 4.8px; line-height: 6.3px; color: #444; }
  .card-contact .row { display: flex; align-items: center; gap: 2px; }
  .card-contact .icon { width: 4px; height: 4px; }
  .card-addr { position: absolute; right: 11px; top: 93px; font-size: 4.6px; line-height: 6.3px; color: #444; text-align: right; }

  /* Business card back */
  .card-back { left: 863px; top: 94px; width: 199px; height: 114px; }
  .card-back .brand { left: 0; right: 0; top: 32px; flex-direction: column; }
  .card-back .brand-circle { width: 34px; height: 34px; border-width: 2px; margin-bottom: 6px; }
  .card-back .brand-name { font-size: 8px; text-align: center; }

  /* Envelope front */
  .envelope-front { left: 576px; top: 247px; width: 542px; height: 235px; }
  .envelope-front .header-accent { width: 250px; height: 60px; }
  .envelope-front .brand { left: 48px; top: 27px; }
  .envelope-front .brand-circle { width: 48px; height: 48px; margin-right: 6px; }
  .envelope-front .brand-name { font-size: 14.5px; }
  .envelope-addr { position: absolute; left: 100px; top: 80px; display: flex; gap: 4px; font-size: 7.8px; line-height: 10.5px; color: #333; }
  .envelope-addr .icon { width: 8px; height: 10px; }
  .recipient-box { position: absolute; left: 298px; top: 102px; width: 211px; height: 66px; border: 1px solid #ececec; border-radius: 5px; padding: 4px 8px; }
  .recipient-box .label { font-size: 7.5px; color: #444; }
  .recipient-box .line { border-bottom: 1px dotted var(--rule); height: 13.5px; }

  /* Envelope back */
  .envelope-back { left: 576px; top: 510px; width: 542px; height: 235px; }
  .flap { position: absolute; left: 0; top: 0; }
  .flap path { fill: none; stroke: #e2e2e2; stroke-width: 1.2; }
</style>
</head>
<body>

<section class="sheet letterhead">
  <div class="header-accent" role="img" aria-label="Decorative blue and grey header wave"></div>
  <div class="brand">
    <span class="brand-circle"></span>
    <span class="brand-name">Harborline Realty</span>
  </div>
  <div class="letter-contact">
    <div class="row"><svg class="icon" viewBox="0 0 10 10"><path d="M2 0h2l1 3-1.5 1a6 6 0 0 0 2.5 2.5L7 5l3 1v2c0 1-1 2-2 2C4 10 0 6 0 2c0-1 1-2 2-2z"/></svg>555-014-2260</div>
    <div class="row"><svg class="icon" viewBox="0 0 10 10"><path d="M0 2h10v6H0z"/></svg>info@harborline.com</div>
    <div class="row"><svg class="icon" viewBox="0 0 10 10"><circle cx="5" cy="5" r="4.5"/></svg>info@harborline.com</div>
    <div class="addr">Po Box 3625, Street Name,<br>City Name, Zip Code - 00000</div>
  </div>
  <div class="letter-body">
    <div class="salutation">Dear Mr. Avery,</div>
    <p>Lorem Ipsum is simply dummy text of the printing and typesetting industry. Lorem Ipsum has been the industry's standard dummy text ever since the 1500s, when an unknown printer took a galley of type and scrambled it to make a type specimen book. It has survived not only five centuries, but also the leap into electronic typesetting, remaining essentially unchanged.</p>
    <p>The standard chunk of Lorem Ipsum used since the 1500s is reproduced below for those interested. Sections 1.10.32 and 1.10.33 from "de Finibus Bonorum et Malorum" by Cicero are also reproduced in their exact original form, accompanied by English versions from the 1914 translation by H. Rackham</p>
    <p>Lorem Ipsum is simply dummy text of the printing and typesetting industry. Lorem Ipsum has been the industry's standard dummy text ever since the 1500s, when an unknown printer took a galley of type and scrambled it to make a type specimen book. It has survived not only five centuries, but also the leap into electronic typesetting, remaining essentially unchanged. It was popularised in the</p>
    <p>The standard chunk of Lorem Ipsum used since the 1500s is reproduced below for those interested. Sections 1.10.32 and 1.10.33 from "de Finibus Bonorum et Malorum" by Cicero are also reproduced in their exact original form, accompanied by English versions from the 1914 translation by H. Rackham</p>
    <p>The standard chunk of Lorem Ipsum used since the 1500s is reproduced below for those interested. Sections 1.10.32 and 1.10.33 from "de Finibus Bonorum et Malorum" by Cicero are also reproduced in their exact original form.</p>
  </div>
  <div class="signature" role="img" aria-label="Handwritten signature"></div>
</section>

<section class="sheet card-front">
  <div class="header-accent" role="img" aria-label="Decorative blue and grey header wave"></div>
  <div class="brand">
    <span class="brand-circle"></span>
    <span class="brand-name">Harborline<br>Realty</span>
  </div>
  <div class="card-holder">
    <div class="name">Dana Mercer</div>
    <div class="role">President</div>
  </div>
  <div class="card-contact">
    <div class="row"><svg class="icon" viewBox="0 0 10 10"><path d="M2 0h2l1 3-1.5 1a6 6 0 0 0 2.5 2.5L7 5l3 1v2c0 1-1 2-2 2C4 10 0 6 0 2c0-1 1-2 2-2z"/></svg>555-014-2260</div>
    <div class="row"><svg class="icon" viewBox="0 0 10 10"><path d="M0 2h10v6H0z"/></svg>info@harborline.com</div>
    <div class="row"><svg class="icon" viewBox="0 0 10 10"><circle cx="5" cy="5" r="4.5"/></svg>www.harborline.com</div>
  </div>
  <div class="card-addr">Po Box 3625, Street Name,<br>City Name, Zip Code - 00000</div>
</section>

<section class="sheet card-back">
  <div class="brand">
    <span class="brand-circle"></span>
    <span class="brand-name">Harborline Realty</span>
  </div>
</section>

<section class="sheet envelope-front">
  <div class="header-accent" role="img" aria-label="Decorative blue and grey header wave"></div>
  <div class="brand">
    <span class="brand-circle"></span>
    <span class="brand-name">Harborline Realty</span>
  </div>
  <div class="envelope-addr">
    <svg class="icon" viewBox="0 0 8 10"><path d="M4 0a4 4 0 0 1 4 4c0 3-4 6-4 6S0 7 0 4a4 4 0 0 1 4-4zm0 2.2a1.8 1.8 0 1 0 0 3.6 1.8 1.8 0 0 0 0-3.6z"/></svg>
    <div>Po. box 201, Street Name,<br>City Name, Zip Code - 00000</div>
  </div>
  <div class="recipient-box">
    <div class="label">To</div>
    <div class="line"></div>
    <div class="line"></div>
    <div class="line"></div>
    <div class="line"></div>
  </div>
</section>

<section class="sheet envelope-back">
  <svg class="flap" width="542" height="62" viewBox="0 0 542 62" aria-hidden="true">
    <path d="M0,30 C0,50 10,58 30,58 L512,58 C532,58 542,50 542,30"/>
  </svg>
</section>

</body>
</html>
```